Velvet Lantern rebranding my business with a new business card

I have my new logo and now I need a refresher on my business cards. I really want something fun and fresh. I like black background or anything to make the color pop.
Logo
Name: Velvet Lantern
Contact Info as stated below:
Mira Pellow
555-013-4762
Logo
Name: Velvet Lantern
Mira Pellow
555-013-4762
fb.me/VelvetLanternbyMira
Instagram: @VelvetLanternbyMira

Industry/Entity Type

Business

Contact Information for Business Card

double-sided. Logo on one side. Contact info on the other.

Requirements
Must have
• Logo
• Name: Velvet Lantern
• Contact Info as stated below:
• Mira Pellow
• 555-013-4762
• fb.me/VelvetLanternbyMira
• fb.me/VelvetLanternbyMira

```html
<!DOCTYPE html>
<html lang="en">
<head>
<meta charset="utf-8">
<title>Velvet Lantern – Business Card</title>
<link rel="stylesheet" href="https://fonts.googleapis.com/css2?family=Source+Sans+3:wght@400;600&display=swap">
<style>
  :root {
    --backdrop: #3b322e;
    --card: #0c0c0c;
    --ink-light: #f2f2f2;
    --accent-pink: #e77bb5;
    --font-main: "Source Sans 3", "Myriad Pro", Arial, sans-serif;
  }
  * { box-sizing: border-box; margin: 0; padding: 0; }
  html, body {
    width: 1200px; height: 844px; overflow: hidden;
    background: var(--backdrop);
    font-family: var(--font-main);
  }
  .canvas {
    position: relative; width: 1200px; height: 844px;
    display: flex; align-items: center; justify-content: center; gap: 40px;
  }
  .card {
    position: relative; width: 540px; height: 309px;
    background: var(--card);
    box-shadow: 0 10px 30px rgba(0,0,0,.45);
  }
  .brand-mark {
    position: absolute; display: flex; align-items: center; gap: 8px;
    color: var(--accent-pink); font-weight: 600; font-size: 24px; white-space: nowrap;
  }
  .brand-mark .dot {
    width: 14px; height: 14px; border-radius: 50%; background: var(--accent-pink);
  }
  .card--front .brand-mark { left: 200px; top: 92px; }
  .card--back .brand-mark { left: 50%; top: 50%; transform: translate(-50%, -50%); font-size: 28px; }

  .contact-list {
    position: absolute; right: 36px; top: 150px;
    list-style: none; text-align: right;
    color: var(--ink-light); font-size: 15px; line-height: 22px;
  }
  .contact-list li { display: flex; justify-content: flex-end; align-items: center; gap: 8px; }
  .contact-list svg { width: 11px; height: 11px; fill: var(--accent-pink); flex: none; }
  .holder-name {
    position: absolute; left: 36px; bottom: 44px;
    color: var(--accent-pink); font-weight: 600; font-size: 22px;
  }
</style>
</head>
<body>
<main class="canvas">
  <section class="card card--front" aria-label="Card front with contact details">
    <div class="brand-mark"><span class="dot"></span>Velvet Lantern</div>
    <ul class="contact-list">
      <li>555-013-4762
        <svg viewBox="0 0 12 12" aria-hidden="true"><path d="M2.5 1 L4.5 1 L5.2 3.5 L4 4.5 Q5 7 7.5 8 L8.5 6.8 L11 7.5 L11 9.5 Q10.5 11 9 11 Q1 10 1 3 Q1 1.5 2.5 1Z"/></svg>
      </li>
      <li>info@youremail.com
        <svg viewBox="0 0 12 12" aria-hidden="true"><path d="M1 2.5 H11 V9.5 H1Z M1.6 3 L6 6.5 L10.4 3" stroke="#0c0c0c" stroke-width=".8"/></svg>
      </li>
      <li>www.website.com
        <svg viewBox="0 0 12 12" aria-hidden="true"><circle cx="6" cy="6" r="5"/><path d="M1 6 H11 M6 1 Q3 6 6 11 Q9 6 6 1" stroke="#0c0c0c" stroke-width=".8" fill="none"/></svg>
      </li>
      <li>fb.me/VelvetLanternbyMira
        <svg viewBox="0 0 12 12" aria-hidden="true"><rect x="2" y="2" width="8" height="8"/></svg>
      </li>
    </ul>
    <p class="holder-name">Mira Pellow</p>
  </section>

  <section class="card card--back" aria-label="Card back with brand name">
    <div class="brand-mark"><span class="dot"></span>Velvet Lantern</div>
  </section>
</main>
</body>
</html>
```